PWRPT design for Company

Project: Develop a pwrpt for QT7lx. This can be just a blank pwrpt with standard templates that we can use to build our content and solutions around.
Website: www.qt7lx.example
Color Pallet: Try to use the color schema from our website.
PWRPT Design Tips: While we are a research-based company, our primary target is schools and school districts. We say our work is RESEARCH, POLICY, AND PRACTICE. I would like images that represent “WHY” our research matters, i.e. students, teachers, and administrators. If you can use images and stock photos that represent students with diverse backgrounds, teachers that are diverse and clearly teaching, and administrators that run a school, university, etc. We are in the process of updating our website, but the color scheme will remain the same.
Additional Information:
We built, researched, and designed, www.brvo-kt.example .
We built, researched, and designed, http://67pwgamma.example/olar/index.html
Target Market(s)
EDUCATION
Industry/Entity Type
It Company
Look and feel

```html
<!DOCTYPE html>
<html lang="en">
<head>
<meta charset="utf-8">
<title>One Col Content – QT7lx</title>
<link rel="stylesheet" href="https://fonts.googleapis.com/css2?family=Montserrat:wght@800&family=Rubik:wght@300;400;500&display=swap">
<style>
  :root {
    --orange: #f86b4b;
    --yellow: #fcd84e;
    --arc: #fbe9a8;
    --ink: #3b3b3b;
    --body: #4a4a4a;
    --footer: #4e5959;
    --paper: #ffffff;
    --on-dark: #ffffff;
  }
  * { margin: 0; padding: 0; box-sizing: border-box; }
  html, body { width: 1200px; height: 677px; overflow: hidden; background: var(--paper); }
  .slide {
    position: relative;
    width: 1200px;
    height: 677px;
    overflow: hidden;
    background: var(--paper);
    font-family: "Rubik", sans-serif;
  }
  .accent-bar {
    position: absolute;
    left: 39px; top: 0;
    width: 453px; height: 6px;
    background: var(--yellow);
  }
  .backdrop-arc {
    position: absolute;
    left: 0; top: 0;
    width: 1200px; height: 677px;
    pointer-events: none;
  }
  .slide-title {
    position: absolute;
    left: 43px; top: 34px;
    font-family: "Montserrat", sans-serif;
    font-weight: 800;
    font-size: 42px;
    color: var(--ink);
    line-height: 1.1;
  }
  .slide-title .highlight { color: var(--orange); }
  .brand {
    position: absolute;
    right: 16px; top: 36px;
    display: flex;
    align-items: center;
    gap: 8px;
    font-family: "Rubik", sans-serif;
    font-weight: 400;
    font-size: 40px;
    line-height: 1;
    color: var(--ink);
  }
  .brand-dot {
    width: 22px; height: 22px;
    border-radius: 50%;
    background: var(--orange);
  }
  .content-column {
    position: absolute;
    left: 57px; top: 140px;
    width: 474px;
  }
  .col-title {
    font-weight: 500;
    font-size: 27px;
    color: var(--orange);
    line-height: 1.2;
    margin-bottom: 2px;
  }
  .col-text {
    font-weight: 300;
    font-size: 15.5px;
    line-height: 29.2px;
    color: var(--body);
    text-align: justify;
    hyphens: auto;
    -webkit-hyphens: auto;
  }
  .col-text + .col-text { margin-top: 29px; }
  .photo-ring {
    position: absolute;
    left: 647px; top: 172px;
    width: 416px; height: 416px;
    border: 1.5px solid var(--orange);
    border-radius: 50%;
  }
  .photo {
    position: absolute;
    left: 663px; top: 188px;
    width: 384px; height: 384px;
    border-radius: 50%;
    background: radial-gradient(circle at 50% 40%, #d9b8a0 0%, #b28a72 40%, #5f7aa6 75%, #c9566f 100%);
  }
  .dot { position: absolute; border-radius: 50%; }
  .dot-yellow { left: 736px; top: 180px; width: 36px; height: 36px; background: var(--yellow); }
  .dot-orange { left: 981px; top: 494px; width: 42px; height: 42px; background: var(--orange); }
  .footer {
    position: absolute;
    left: 0; bottom: 0;
    width: 1200px; height: 26px;
    background: var(--footer);
    color: var(--on-dark);
    font-size: 14px;
    font-weight: 400;
    line-height: 26px;
    padding-left: 11px;
  }
</style>
</head>
<body>
<main class="slide">
  <svg class="backdrop-arc" viewBox="0 0 1200 677" aria-hidden="true">
    <path d="M0 112 C 150 180, 250 350, 232 520 C 224 590, 198 640, 170 677" fill="none" stroke="var(--arc)" stroke-width="1.5"/>
  </svg>

  <div class="accent-bar"></div>

  <h1 class="slide-title">ONE <span class="highlight">COL CONTENT</span></h1>

  <div class="brand"><span class="brand-dot"></span>QT7lx</div>

  <section class="content-column">
    <h2 class="col-title">Col Title</h2>
    <p class="col-text">Lorem Ipsum is simply dummy text of the printing and typesetting industry. Lorem Ipsum has been the industry's standard dummy text ever since the 1500s, when an unknown printer took a galley of type and scrambled it to make a type specimen book. It has survived not only five centuries, but also the leap into electronic typesetting, remaining essentially unchanged. Lorem Ipsum is simply dummy text of the printing and typesetting industry.</p>
    <p class="col-text">Lorem Ipsum has been the industry's standard dummy text ever since the 1500s, when an unknown printer took a galley of type and scrambled it to make a type specimen book. It has survived not only five centuries, but also the leap into electronic typesetting, remaining essentially unchanged.</p>
  </section>

  <div class="photo-ring"></div>
  <div class="photo" role="img" aria-label="Photo of a diverse group of smiling students giving a thumbs up"></div>
  <div class="dot dot-yellow"></div>
  <div class="dot dot-orange"></div>

  <footer class="footer">Copyright @Text</footer>
</main>
</body>
</html>
```